Coastline Premier Retreats Business Card Design

Design a business card for Coastline Premier Retreats. Look at the website for colors and reference. Card should have logo, name, title, office number, mobile number, email, URL and a tagline like, "Luxury Hotel & Resort Email Marketing" (This might change).

https://www.coastlinepremierretreats.example

The rest I will leave up to your imagination.

Contact Information for Business Card

Logo, name, title, office number, mobile number, email, URL and a tagline like, "Luxury Hotel & Resort Email Marketing" (This might change).

```html
<!DOCTYPE html>
<html lang="en">
<head>
<meta charset="utf-8">
<title>Coastline Premier Retreats — Business Card</title>
<link href="https://fonts.googleapis.com/css2?family=Maven+Pro:wght@700&family=Montserrat:wght@400;700&display=swap" rel="stylesheet">
<style>
  :root {
    --bg: #e9e8ea;
    --card: #222224;
    --orange: #f27623;
    --white: #ffffff;
    --stripe-light: #f2f2f2;
    --text: #f4f4f4;
  }
  * { margin: 0; padding: 0; box-sizing: border-box; }
  html, body { width: 1200px; height: 1108px; overflow: hidden; background: var(--bg); }
  .canvas { position: relative; width: 1200px; height: 1108px; }
  .card {
    position: absolute; width: 730px; height: 438px;
    background: var(--card); overflow: hidden;
  }
  .card--front { left: 238px; top: 67px; }
  .card--back { left: 244px; top: 581px; }
  .card__band { position: absolute; left: 0; bottom: 0; width: 730px; height: 10px; }

  .brand {
    display: flex; align-items: center; gap: 10px;
    font-family: "Montserrat", sans-serif; font-weight: 700;
    color: var(--white); text-transform: uppercase; white-space: nowrap;
  }
  .brand__square { background: var(--orange); flex: none; }
  .card--front .brand { position: absolute; right: 36px; top: 60px; font-size: 19px; letter-spacing: 1px; }
  .card--front .brand__square { width: 16px; height: 16px; }
  .card--back .brand {
    position: absolute; left: 0; right: 0; top: 196px; justify-content: center;
    font-size: 29px; letter-spacing: 1.5px;
  }
  .card--back .brand__square { width: 24px; height: 24px; }

  .person { position: absolute; left: 34px; top: 228px; }
  .person__name {
    font-family: "Maven Pro", sans-serif; font-weight: 700; font-size: 26px;
    color: var(--orange); line-height: 1;
  }
  .person__title {
    font-family: "Montserrat", sans-serif; font-size: 15px; color: var(--text);
    margin-top: 6px;
  }
  .divider { position: absolute; left: 34px; top: 286px; width: 663px; height: 2px; background: var(--orange); }

  .contacts { position: absolute; left: 36px; top: 305px; list-style: none; }
  .contacts li {
    display: flex; align-items: center; gap: 14px; height: 25px;
    font-family: "Montserrat", sans-serif; font-size: 15.5px; color: var(--text);
  }
  .contacts svg { width: 16px; height: 16px; flex: none; fill: var(--orange); }

  .address {
    position: absolute; left: 488px; top: 356px;
    font-family: "Montserrat", sans-serif; font-size: 15.5px; line-height: 22px; color: var(--text);
  }
  .tagline {
    position: absolute; left: 0; right: 0; top: 362px; text-align: center;
    font-family: "Maven Pro", sans-serif; font-weight: 700; font-size: 16px; color: var(--orange);
  }
</style>
</head>
<body>
<main class="canvas">
  <section class="card card--front">
    <div class="brand"><span class="brand__square"></span>Coastline Premier Retreats</div>

    <div class="person">
      <div class="person__name">Jordan Haleway</div>
      <div class="person__title">Owner</div>
    </div>
    <div class="divider"></div>

    <ul class="contacts">
      <li>
        <svg viewBox="0 0 16 16" aria-hidden="true"><path d="M2 6c0-2 3-3.5 6-3.5S14 4 14 6v1h-3V5.5H5V7H2z"/><path d="M4 8h8l1.5 5.5h-11z"/></svg>
        555.210.4830 x 112
      </li>
      <li>
        <svg viewBox="0 0 16 16" aria-hidden="true"><path d="M4.5 0.5h7a1 1 0 0 1 1 1v13a1 1 0 0 1-1 1h-7a1 1 0 0 1-1-1v-13a1 1 0 0 1 1-1zM5 2.5v10h6v-10zM7 13.3h2v1H7z"/></svg>
        555.384.9172
      </li>
      <li>
        <svg viewBox="0 0 16 16" aria-hidden="true"><path d="M1 3h14v1.5L8 9 1 4.5z"/><path d="M1 6.2 8 10.7l7-4.5V13H1z"/></svg>
        info@coastlinepremierretreats.example
      </li>
      <li>
        <svg viewBox="0 0 16 16" aria-hidden="true"><circle cx="8" cy="8" r="7"/><path d="M4 4.5c1.5 0 2 1 3 1.5s.5 2-1 2.5-1 2.5-2.5 2C2.5 9 2.5 6 4 4.5zM10 9c1.5-.5 3 0 3 1s-1.5 2.5-3 3c-1 0-.5-3.5 0-4z" fill="#222224"/></svg>
        www.coastlinepremierretreats.example
      </li>
    </ul>

    <address class="address" style="font-style:normal">410 Harbor Rd. Suite 12<br>Bayview, CA 90210</address>

    <svg class="card__band" viewBox="0 0 730 10" preserveAspectRatio="none" aria-hidden="true">
      <rect x="0" y="0" width="488" height="10" fill="var(--orange)"/>
      <polygon points="490,10 500,0 730,0 730,10" fill="var(--stripe-light)"/>
    </svg>
  </section>

  <section class="card card--back">
    <div class="brand"><span class="brand__square"></span>Coastline Premier Retreats</div>
    <p class="tagline">Luxury Hotel &amp; Resort Email Marketing</p>
    <svg class="card__band" viewBox="0 0 730 10" preserveAspectRatio="none" aria-hidden="true">
      <rect x="0" y="0" width="472" height="10" fill="var(--orange)"/>
      <polygon points="474,10 484,0 730,0 730,10" fill="var(--stripe-light)"/>
    </svg>
  </section>
</main>
</body>
</html>
```